Redesign 2016 Digital Marketing Website and Convert to Wordpress

Technology needed to integrate:

- redesign and convert to wordpress
- gravity forms
- malware and hacker defense / honeypot (must be very secure from hackers)
- I want gravity forms to be a flow that asks many questions with icons and progress bar.
- 1 home page design
- 1 blog design
- 1 design for internal page content
- 1 multi step gravity form
I want to focus on SMB's. We are a marketing agency thats been around since 2016.

Site is: tallpine.agency

I am looking to redesign the homepage, blog page and services page. The services page will be a template for all inner pages of the site. All content needs to be moved into the new design.

I want to get ride of the weird video.

I need you to install gravity forms pro model so we can pass utms.

I need the gravity form to be a multi step form with icons.

All "contact us" or "get a free assesments" call to actions will go to this form only.

step 1:
what is your website

step 2:
what industry are you in
- option
- Home Services
- Legal
- Ecommerce
- Lead Gen

No matter which one they select its going to produce a differnt calculator for them.

Law:
How many leads did you get last month
how much is each ase worth on average
How much revenue do you want to make

Home servicse:
How many bookings did you get last month
How much is each service worht on average
How much revenue do you wangt to make

Ecommerce:
What is your average order value
How muny purchases did you have last month
How much revenue did you drive
How much revenue do you want to drive

For lead gen:
How many leads did you get lawt month
How much revenue did they generate

Step 3:
What is your current advertising budget

step 4:
Do you have a CRM and if so what is it

Step 5:
What is your personal informagtion
name
email
phone

Let me know if this is enough to get you going

Small and medium sized law firms, ecommerce, home services and lead gen customers.

We are a digital marketing agency

• Use whats on the current site and improve upon it

• Must be very secure, developed into a wordpress website. using gravity forms. remove my photo and my staffs photo, depersonalize it so it doesnt mention me or sam crolley. Use the same color scheme. I am looking to redesign the homepage, blog page and services page. The services page will be a template for all inner pages of the site. All content needs to be moved into the new design. I want to get ride of the weird video. I need you to install gravity forms pro model so we can pass utms. I need the gravity form to be a multi step form with icons. All "contact us" or "get a free assesments" call to actions will go to this form only. step 1: what is your website step 2: what industry are you in - option - Home Services - Legal - Ecommerce - Lead Gen No matter which one they select its going to produce a differnt calculator for them. Law: How many leads did you get last month how much is each ase worth on average How much revenue do you want to make Home servicse: How many bookings did you get last month How much is each service worht on average How much revenue do you wangt to make Ecommerce: What is your average order value How muny purchases did you have last month How much revenue did you drive How much revenue do you want to drive For lead gen: How many leads did you get lawt month How much revenue did they generate How much revenue do you want to make Step 3: What is your current advertising budget step 4: Do you have a CRM and if so what is it Step 5: What is your personal informagtion name email phone Let me know if this is enough to get you going
• SHOULD NOT BE SLOPPY, I AM LOOKING FOR ATTENTION TO DETAIL.

```html
<!DOCTYPE html>
<html lang="en">
<head>
<meta charset="utf-8">
<title>Tall Pine Growth Marketing – Get a Free Assessment</title>
<link href="https://fonts.googleapis.com/css2?family=Poppins:wght@300;400;500;600;700;800&display=swap" rel="stylesheet">
<style>
  :root{
    --brand:#7a1517;
    --brand-deep:#5e0f11;
    --ink:#2f2f2f;
    --nav:#323232;
    --muted:#555;
    --line:#e2e2e2;
    --badge:#dcdcdc;
    --white:#fff;
  }
  *{box-sizing:border-box;margin:0;padding:0}
  html,body{width:965px;height:1200px;overflow:hidden;background:var(--white)}
  body{font-family:'Poppins',sans-serif;color:var(--ink);position:relative}
  .abs{position:absolute}

  /* header */
  .site-header{position:absolute;left:0;top:0;width:965px;height:73px}
  .brand{position:absolute;left:60px;top:12px;display:flex;align-items:center;gap:12px}
  .brand-mark{width:48px;height:48px;border-radius:50%;border:3px solid var(--brand);background:var(--white)}
  .brand-name{font-weight:300;font-size:19px;letter-spacing:2px;color:var(--muted);line-height:1}
  .brand-tag{font-size:7px;letter-spacing:4px;color:var(--muted);margin-top:6px;font-weight:400}
  .call-line{position:absolute;left:454px;top:26px;font-size:14px;font-weight:600;color:#444}
  .call-line span{color:var(--brand);font-weight:700}
  .btn-revenue{position:absolute;left:725px;top:17px;width:181px;height:39px;background:var(--brand);color:var(--white);font-size:12px;font-weight:600;display:flex;align-items:center;justify-content:center;letter-spacing:.3px}

  .main-nav{position:absolute;left:0;top:73px;width:965px;height:43px;background:var(--nav);display:flex;justify-content:center;align-items:center;gap:37.5px}
  .main-nav a{color:var(--white);text-decoration:none;font-size:11.5px;letter-spacing:.2px}

  /* assessment */
  .page-title{position:absolute;left:60px;top:158px;font-size:30px;font-weight:800;letter-spacing:.3px;color:var(--ink)}
  .title-rule{position:absolute;left:60px;top:206px;width:75px;height:3px;background:var(--brand)}
  .field-label{position:absolute;left:149px;top:248px;font-size:13px;font-weight:500;color:var(--ink)}
  .step{position:absolute;left:56px;top:285px;display:flex;align-items:center;gap:10px}
  .step-dot{width:22px;height:22px;border-radius:50%;background:var(--brand);box-shadow:0 0 0 3px #e3e3e3}
  .step-text{font-size:13px;font-weight:700;color:var(--brand)}
  .field-input{position:absolute;left:149px;top:275px;width:398px;height:41px;border:1px solid #bbb;font-size:9.5px;color:#333;padding-left:11px;display:flex;align-items:center}
  .btn-next{position:absolute;left:149px;top:327px;width:192px;height:40px;background:var(--nav);color:var(--white);font-size:16px;font-weight:700;display:flex;align-items:center;justify-content:center;gap:10px;letter-spacing:.5px}

  /* cta band */
  .cta-band{position:absolute;left:0;top:420px;width:965px;height:276px;background:radial-gradient(ellipse at 45% 40%,#8a2224 0%,#6e1416 45%,var(--brand-deep) 100%)}
  .cta-title{position:absolute;left:60px;top:509px;font-size:30.5px;font-weight:800;color:var(--white);letter-spacing:.4px}
  .cta-sub{position:absolute;left:59px;top:555px;font-size:17px;font-weight:400;color:var(--white)}
  .cta-rule{position:absolute;left:60px;top:597px;width:75px;height:3px;background:var(--white)}
  .cta-btn{position:absolute;left:688px;width:219px;height:46px;border:1.5px solid var(--white);color:var(--white);font-size:11.5px;font-weight:600;display:flex;align-items:center;justify-content:center}
  .cta-or{position:absolute;left:783px;top:542px;width:28px;height:28px;border-radius:50%;border:1.5px solid var(--white);background:#1e1e1e;color:var(--white);font-size:10px;font-weight:600;display:flex;align-items:center;justify-content:center}

  /* trust row */
  .trust-row{position:absolute;left:0;top:696px;width:965px;height:125px;border-bottom:1px solid var(--line)}
  .badge-rect{position:absolute;left:334px;top:29px;width:166px;height:71px;border-radius:6px;background:var(--badge)}
  .badge-circle{position:absolute;left:551px;top:28px;width:72px;height:72px;border-radius:50%;background:var(--badge)}
  .follow-title{position:absolute;left:711px;top:726px;font-size:15px;font-weight:500;color:#333;letter-spacing:.5px}
  .social{position:absolute;top:763px;width:24px;height:24px;border-radius:50%;background:#333}

  /* footer columns */
  .col-title{position:absolute;top:851px;font-size:19px;font-weight:700;color:#444}
  .col-links{position:absolute;top:886px;list-style:none}
  .col-links li{font-size:10.6px;color:#444;line-height:26.4px;letter-spacing:.2px}
  .col-links.guides li{line-height:17.4px;margin-bottom:9px}
  .bottom-rule{position:absolute;left:0;top:1137px;width:965px;height:1px;background:var(--line)}
  .copyright{position:absolute;left:0;top:1163px;width:965px;text-align:center;font-size:10.8px;color:#444}
</style>
</head>
<body>

<header class="site-header">
  <div class="brand">
    <div class="brand-mark"></div>
    <div>
      <div class="brand-name">TALL PINE</div>
      <div class="brand-tag">GROWTH MARKETING</div>
    </div>
  </div>
  <div class="call-line">OR CALL US NOW : <span>(480) 555-0147</span></div>
  <div class="btn-revenue">GROW YOUR REVENUE</div>
</header>

<nav class="main-nav">
  <a>HOME</a><a>ABOUT</a><a>INDUSTRIES</a><a>SERVICES</a><a>RESOURCES</a><a>TRAINING</a><a>BLOG</a><a>CONTACT US</a>
</nav>

<section class="assessment">
  <h1 class="page-title">GET A FREE ASSESSMENTS</h1>
  <div class="title-rule"></div>
  <div class="field-label">What is your website</div>
  <div class="step"><div class="step-dot"></div><div class="step-text">STEP 1</div></div>
  <div class="field-input">Enter business name</div>
  <div class="btn-next">NEXT
    <svg width="9" height="14" viewBox="0 0 9 14"><path d="M1.5 1.5 7 7l-5.5 5.5" fill="none" stroke="#fff" stroke-width="1.6"/></svg>
  </div>
</section>

<section>
  <div class="cta-band" role="img" aria-label="Red-tinted photo of hands working on a laptop showing analytics charts"></div>
  <h2 class="cta-title">CAN WE HELP YOUR BUSINESS GROW?</h2>
  <p class="cta-sub">Let’s have a friendly chat to find out.</p>
  <div class="cta-rule"></div>
  <div class="cta-btn" style="top:484px">Get a Free Consultation</div>
  <div class="cta-or">Or</div>
  <div class="cta-btn" style="top:586px">Give us a call: (480) 555-0147</div>
</section>

<section class="trust-row">
  <div class="brand" style="top:39px">
    <div class="brand-mark"></div>
    <div>
      <div class="brand-name">TALL PINE</div>
      <div class="brand-tag">GROWTH MARKETING</div>
    </div>
  </div>
  <div class="badge-rect" role="img" aria-label="Partner program badge"></div>
  <div class="badge-circle" role="img" aria-label="Review listing badge"></div>
</section>
<div class="follow-title">FOLLOW US</div>
<div class="social" style="left:711px" role="img" aria-label="Social profile"></div>
<div class="social" style="left:748px" role="img" aria-label="Social profile"></div>
<div class="social" style="left:788px" role="img" aria-label="Social profile"></div>
<div class="social" style="left:834px" role="img" aria-label="Social profile"></div>
<div class="social" style="left:880px" role="img" aria-label="Social profile"></div>

<footer>
  <h3 class="col-title" style="left:60px">QUICK LINKS</h3>
  <ul class="col-links" style="left:60px">
    <li>About</li><li>Industries</li><li>Services</li><li>Resources</li><li>Training</li><li>Blog</li><li>Contact Us</li>
  </ul>
  <h3 class="col-title" style="left:256px">SERVICES</h3>
  <ul class="col-links" style="left:256px">
    <li>Programmatic Advertising</li><li>Search Engine Marketing (SEM)</li><li>Search Engine Optimization (SEO)</li><li>Content Marketing</li><li>Email Marketing</li><li>Paid Search Advertising</li><li>Paid Social Advertising</li>
  </ul>
  <h3 class="col-title" style="left:494px">INDUSTRIES</h3>
  <ul class="col-links" style="left:494px">
    <li>Ecommerce</li><li>Electricians</li><li>Financial Services Marketing</li><li>Home Builders</li><li>Home Services</li><li>Hvac Companies</li><li>Cosmetic Surgery Centers</li><li>Dental Marketing</li>
  </ul>
  <h3 class="col-title" style="left:710px">GUIDES</h3>
  <ul class="col-links guides" style="left:710px;top:890px">
    <li>Ultimate Guide On Growing Your<br>Medical Practice Business</li>
    <li>Legal Marketing Strategy Guide For<br>Law Firm Offices</li>
    <li>Ultimate Short Video Ads Guide To<br>Skyrocket Your Leads And Sales</li>
    <li>Ultimate Guide To Search<br>Engine Queries</li>
  </ul>
  <div class="bottom-rule"></div>
  <p class="copyright">Copyright © 2024 CompanyName &nbsp;All Rights Reserved. Privacy Policy, Terms Of Use, Press &amp; Media, Cookie Policy</p>
</footer>

</body>
</html>
```